Home Loan Introducer needs logo/business cards

We need a simple but classy logo for business cards and flyers. The business is a home loan referral business that is called an Introducer. The business name is "The Harborline".
I was thinking very simple and straight to the point on the front with "Home Loans" the only thing on the front with a nice background colour/s.
Then on the back, "The Harborline"
and "Quality Customer Service"
and "Email, text or call welcome"
and then my name, email address and phone number.
Updates
Thank you for all the designs :-)
Target Market(s)
Home buyers.
Home owners.
Investors.
Industry/Entity Type
Loan
Look and feel

```html
<!DOCTYPE html>
<html lang="en">
<head>
<meta charset="utf-8">
<title>The Harborline – Business Cards</title>
<link rel="stylesheet" href="https://fonts.googleapis.com/css2?family=Play:wght@400;700&family=Dosis:wght@300;400&display=swap">
<style>
  :root {
    --stage: #c8c8c8;
    --blue: #0467b1;
    --orange: #fdac35;
    --orange-light: #ffe2b4;
    --white: #ffffff;
    --shadow: rgba(0, 0, 0, 0.45);
  }
  html, body {
    margin: 0;
    padding: 0;
    overflow: hidden;
  }
  body {
    width: 1160px;
    height: 1200px;
    background: var(--stage);
    position: relative;
    font-family: "Dosis", sans-serif;
  }
  .card {
    position: absolute;
    left: 129px;
    width: 867px;
    height: 526px;
    box-shadow: 3px 4px 6px var(--shadow);
    overflow: hidden;
  }

  /* Front */
  .card--front {
    top: 47px;
    background: var(--blue);
  }
  .front-band {
    position: absolute;
    left: 0;
    right: 0;
    top: 183px;
    height: 208px;
    background: var(--white);
    top: 182px;
    height: 206px;
  }
  .front-band {
    top: 183px;
    height: 204px;
  }
  .front-label {
    position: absolute;
    left: 0;
    right: 3px;
    top: 190px;
    height: 145px;
    background: var(--orange);
    border-radius: 0 12px 12px 0;
  }
  .front-title {
    position: absolute;
    left: 71px;
    top: 196px;
    margin: 0;
    font-family: "Play", sans-serif;
    font-weight: 700;
    font-size: 117px;
    line-height: 130px;
    letter-spacing: 1px;
    color: var(--white);
    white-space: nowrap;
  }
  .front-title .accent {
    color: var(--blue);
    margin-left: 22px;
  }

  /* Back */
  .card--back {
    top: 613px;
    background: var(--white);
  }
  .back-edge {
    position: absolute;
    left: 0;
    top: 0;
    width: 71px;
    height: 100%;
    background: var(--blue);
  }
  .back-panel {
    position: absolute;
    left: 480px;
    top: 0;
    right: 0;
    height: 100%;
    background: radial-gradient(circle at 85% 48%, var(--orange-light) 0%, #ffc873 22%, var(--orange) 55%);
  }
  .brand {
    position: absolute;
    left: 71px;
    width: 409px;
    top: 160px;
    text-align: center;
  }
  .brand-mark {
    display: block;
    margin: 0 auto 26px;
  }
  .brand-name {
    margin: 0;
    font-family: "Play", sans-serif;
    font-weight: 700;
    font-size: 40px;
    line-height: 44px;
    color: var(--blue);
    text-transform: uppercase;
  }
  .contact {
    position: absolute;
    left: 499px;
    top: 159px;
    color: var(--white);
    font-weight: 300;
  }
  .contact p { margin: 0; }
  .tagline {
    font-size: 22px;
    line-height: 26px;
  }
  .contact-company {
    margin-top: 14px !important;
    font-size: 29px;
    line-height: 34px;
    color: var(--blue);
    font-weight: 400;
    width: 299px;
    padding-bottom: 8px;
    border-bottom: 2px dotted var(--blue);
  }
  .contact-name {
    margin-top: 10px !important;
    font-size: 28px;
    line-height: 32px;
    font-style: italic;
  }
  .contact-line {
    font-size: 21px;
    line-height: 27px;
    font-weight: 400;
  }
</style>
</head>
<body>

  <section class="card card--front" aria-label="Card front">
    <div class="front-band"></div>
    <div class="front-label"></div>
    <h1 class="front-title">HOME<span class="accent">LOAN</span></h1>
  </section>

  <section class="card card--back" aria-label="Card back">
    <div class="back-edge"></div>
    <div class="back-panel"></div>

    <div class="brand">
      <svg class="brand-mark" width="130" height="130" viewBox="0 0 130 130" aria-hidden="true">
        <circle cx="65" cy="65" r="62" fill="var(--blue)"/>
      </svg>
      <p class="brand-name">The Harborline</p>
    </div>

    <div class="contact">
      <p class="tagline">Quality Customer Service</p>
      <p class="tagline">Email, text or call are Welcome</p>
      <p class="contact-company">The Harborline</p>
      <p class="contact-name">Martin Kessler</p>
      <p class="contact-line">hello@theharborline.com</p>
      <p class="contact-line">+639170004821</p>
    </div>
  </section>

</body>
</html>
```